Business Card for premium dental clinic

We are a premium dental clinic based in Brasov, Romania with more than 15 year on the market, providing quality dental treatment made by a team of more specialized dentists, working with modern equipment as a solution to beautiful and healthy teeth.

Our current logo for the clinic use 2 square with colors black and gold - dr Ternisu - studio, using family fonts Bodoni, Myriad Pro and Segoe Print.
Depending on the printing we used some gold CMYK background or gold foil picture background or a gold gradient.
We want a business card:
- eye catching business card
- distinguished business card
- premium design
- to keep the color scheme of black and gold
- to attract the customers to spent time reading the information
- modern concept

```html
<!DOCTYPE html>
<html lang="en">
<head>
<meta charset="UTF-8">
<title>Lumina Dental Clinic – Business Card</title>
<link href="https://fonts.googleapis.com/css2?family=Montserrat:wght@400;500;700&family=Oswald:wght@300;400&display=swap" rel="stylesheet">
<style>
  :root {
    --stage: #2b2b2b;
    --card: #0d0d0d;
    --ink-black: #000000;
    --white: #ffffff;
    --gold: #e3b93a;
    --gold-light: #f7dc72;
    --gold-deep: #b8841c;
    --name-gold: #f0d04a;
  }
  * { box-sizing: border-box; margin: 0; padding: 0; }
  html, body { width: 1200px; height: 900px; overflow: hidden; }
  body { background: var(--stage); position: relative; font-family: "Montserrat", sans-serif; }

  .card {
    position: absolute;
    left: 260px;
    width: 680px;
    height: 388px;
    background: var(--card);
    overflow: hidden;
    box-shadow: 0 10px 24px rgba(0,0,0,.45);
  }
  .card--front { top: 36px; }
  .card--back  { top: 476px; }

  .gold-bands { position: absolute; inset: 0; width: 680px; height: 388px; }

  /* Front */
  .brand-frame {
    position: absolute; left: 118px; top: 64px;
    width: 480px; height: 236px;
    border: 2px solid var(--white);
    display: flex;
  }
  .foil-panel {
    width: 50%; height: 100%;
    background: radial-gradient(circle at 35% 40%, var(--gold-light), var(--gold) 45%, var(--gold-deep) 100%);
    position: relative;
  }
  .doctor-label {
    position: absolute; left: 52px; top: 92px;
    width: 186px; height: 62px;
    background: var(--white);
    display: flex; align-items: flex-end; justify-content: center;
    padding-bottom: 10px;
    font-family: "Oswald", sans-serif; color: #222;
  }
  .doctor-label .prefix { font-size: 20px; font-weight: 300; margin-right: 2px; }
  .doctor-label .surname { font-size: 36px; font-weight: 400; line-height: 1; }
  .brand-panel {
    width: 50%; height: 100%;
    background: var(--ink-black);
    position: relative;
  }
  .brand-name {
    position: absolute; left: 30px; top: 66px;
    font-size: 40px; font-weight: 500; color: var(--white);
    letter-spacing: 1px;
  }
  .brand-tagline {
    position: absolute; right: 14px; bottom: 22px;
    font-family: "Oswald", sans-serif; font-size: 20px; color: var(--white);
    letter-spacing: .5px;
  }

  /* Back */
  .rule { position: absolute; height: 1px; background: #cfcfcf; }
  .rule--top { left: 300px; top: 92px; width: 340px; }
  .rule--mid { left: 120px; top: 272px; width: 300px; }
  .brand-block {
    position: absolute; left: 30px; top: 100px;
    width: 250px; height: 118px;
    background: var(--ink-black);
    display: flex; align-items: center; justify-content: center;
  }
  .brand-block .brand-name { position: static; font-size: 48px; }
  .doctor-name {
    position: absolute; left: 118px; top: 232px;
    font-size: 26px; font-weight: 700; color: var(--name-gold);
  }
  .contacts { position: absolute; left: 136px; top: 280px; list-style: none; }
  .contacts li {
    display: flex; align-items: center; gap: 12px;
    height: 20px; font-size: 15px; color: var(--white);
  }
  .contacts svg { width: 14px; height: 14px; flex: none; }
  .address {
    position: absolute; right: 30px; top: 248px;
    text-align: right; font-size: 15px; line-height: 1.2; color: var(--name-gold);
  }
</style>
</head>
<body>

<section class="card card--front">
  <div class="brand-frame">
    <div class="foil-panel" role="img" aria-label="Gold foil texture background">
      <div class="doctor-label"><span class="prefix">dr.</span><span class="surname">ternisu</span></div>
    </div>
    <div class="brand-panel">
      <span class="brand-name">lumina</span>
      <span class="brand-tagline">dental clinic</span>
    </div>
  </div>
  <svg class="gold-bands" viewBox="0 0 680 388" aria-hidden="true">
    <defs>
      <linearGradient id="goldBandFront" x1="0" x2="1">
        <stop offset="0" stop-color="#b8841c"/>
        <stop offset=".5" stop-color="#f7dc72"/>
        <stop offset="1" stop-color="#c9972a"/>
      </linearGradient>
    </defs>
    <polygon points="0,352 300,352 306,366 0,366" fill="url(#goldBandFront)"/>
    <polygon points="300,344 330,330 336,344 306,358" fill="#9a6d15"/>
    <polygon points="330,328 680,322 680,330 336,336" fill="url(#goldBandFront)"/>
  </svg>
</section>

<section class="card card--back">
  <div class="rule rule--top"></div>
  <div class="brand-block"><span class="brand-name">lumina</span></div>
  <div class="doctor-name">dr.ternisu</div>
  <div class="rule rule--mid"></div>
  <ul class="contacts">
    <li>
      <svg viewBox="0 0 16 16" aria-hidden="true"><path d="M4 1.5l2.5 3-1.5 1.5c.8 2 2.5 3.7 4.5 4.5l1.5-1.5 3 2.5-1.5 2.5C7.5 14 2 8.5 1.5 3z" fill="none" stroke="#e3b93a" stroke-width="1.3"/></svg>
      +00 000 417 5260
    </li>
    <li>
      <svg viewBox="0 0 16 16" aria-hidden="true"><rect x="4.5" y="1" width="7" height="14" rx="1.3" fill="none" stroke="#e3b93a" stroke-width="1.3"/><circle cx="8" cy="12.5" r=".9" fill="#e3b93a"/></svg>
      +00 000 417 5260
    </li>
    <li>
      <svg viewBox="0 0 16 16" aria-hidden="true"><rect x="1" y="3.5" width="14" height="9" fill="none" stroke="#e3b93a" stroke-width="1.3"/><path d="M1 3.5l7 5 7-5" fill="none" stroke="#e3b93a" stroke-width="1.3"/></svg>
      info@luminadent.com
    </li>
    <li>
      <svg viewBox="0 0 16 16" aria-hidden="true"><circle cx="8" cy="8" r="6.5" fill="none" stroke="#e3b93a" stroke-width="1.3"/><ellipse cx="8" cy="8" rx="3" ry="6.5" fill="none" stroke="#e3b93a" stroke-width="1.1"/><path d="M1.5 8h13M2.5 5h11M2.5 11h11" stroke="#e3b93a" stroke-width="1"/></svg>
      www.luminadent.com
    </li>
  </ul>
  <p class="address">88 Linden Avenue<br>Brasov 500030</p>
  <svg class="gold-bands" viewBox="0 0 680 388" aria-hidden="true">
    <defs>
      <linearGradient id="goldBandBack" x1="0" x2="1">
        <stop offset="0" stop-color="#b8841c"/>
        <stop offset=".5" stop-color="#f7dc72"/>
        <stop offset="1" stop-color="#c9972a"/>
      </linearGradient>
    </defs>
    <polygon points="150,368 440,360 440,365 150,373" fill="url(#goldBandBack)"/>
    <polygon points="430,322 446,314 446,334 430,340" fill="#9a6d15"/>
    <polygon points="446,312 680,300 680,314 446,326" fill="url(#goldBandBack)"/>
  </svg>
</section>

</body>
</html>
```